Meridian Crestline Motors *

Professional business cards for our auto wholesale dealership.

Target Market(s)

New and used cars sales managers and middle class to higher end private party buyers.

Industry/Entity Type

Automotive

Contact Information for Business Card

Meridian Crestline Motors
Darnell R Okonski
Owner
(555) 304-6618
mercrestmotors@quillbox.example
Dealer Lic # 48265

Logo Text

Meridian Crestline Motors, Mer Crest Motors, MCM, etc

Font styles to use
Serif
Sans Serif

Colors

Designer to choose colors to be used in the design.

Requirements
Must have
• A professional, but not pretentious, look
Nice to have
• It might be nice to see "MCM" in a shape form i.e. circle, triangle, etc in the corner or background somehwere
Should not have
• bright "girly" colors

```html
<!DOCTYPE html>
<html lang="en">
<head>
<meta charset="utf-8">
<title>Meridian Crestline Motors – Business Card</title>
<link rel="stylesheet" href="https://fonts.googleapis.com/css2?family=Open+Sans:wght@400;600;700&display=swap">
<style>
  :root {
    --page: #e9eaeb;
    --card-light: #f7f7f7;
    --card-mid: #d9dadb;
    --lime: #8cc21f;
    --lime-dark: #78a814;
    --ink: #262b33;
    --ink-soft: #4a4f57;
    --photo-light: #e6e7e8;
    --photo-dark: #6d7076;
  }
  html, body {
    margin: 0;
    width: 1200px;
    height: 1200px;
    overflow: hidden;
    background: var(--page);
    font-family: "Open Sans", Arial, sans-serif;
  }
  .sheet {
    position: relative;
    width: 1200px;
    height: 1200px;
  }
  .card {
    position: absolute;
    left: 160px;
    width: 880px;
    height: 503px;
    border-radius: 26px;
    overflow: hidden;
    background: radial-gradient(ellipse at 35% 30%, var(--card-light) 0%, var(--card-mid) 100%);
    box-shadow: 0 10px 30px rgba(0,0,0,.18);
  }
  .card--front { top: 70px; }
  .card--back { top: 627px; }
  .lime-band {
    position: absolute;
    left: 0; right: 0; bottom: 0;
    height: 30px;
    background: var(--lime);
  }
  .rule {
    position: absolute;
    background: var(--ink);
  }
  .brand {
    position: absolute;
    display: flex;
    align-items: center;
    gap: 18px;
  }
  .brand__dot {
    width: 78px;
    height: 78px;
    border-radius: 50%;
    background: var(--lime);
    border: 3px solid var(--ink);
    box-sizing: border-box;
    flex: none;
  }
  .brand__name {
    font-weight: 700;
    font-size: 34px;
    line-height: 1.05;
    color: var(--ink);
    letter-spacing: .5px;
  }
  .person {
    position: absolute;
    left: 70px;
    top: 212px;
  }
  .person__bar {
    position: absolute;
    left: -24px;
    top: 8px;
    width: 12px;
    height: 36px;
    border-radius: 6px;
    background: var(--lime);
  }
  .person__name {
    margin: 0;
    font-size: 32px;
    font-weight: 400;
    color: var(--ink);
  }
  .person__role {
    margin: 0;
    font-size: 20px;
    color: var(--ink-soft);
  }
  .contact {
    position: absolute;
    left: 46px;
    top: 316px;
    margin: 0;
    padding: 0;
    list-style: none;
    font-size: 17px;
    color: var(--ink-soft);
  }
  .contact li {
    display: flex;
    align-items: center;
    gap: 10px;
    height: 32px;
  }
  .contact svg { width: 18px; height: 18px; flex: none; }
  .contact .plain { padding-left: 28px; }
  .photo-round {
    position: absolute;
    left: 598px;
    top: 100px;
    width: 220px;
    height: 220px;
    border-radius: 50%;
    border: 5px solid var(--ink);
    box-sizing: border-box;
    background: radial-gradient(circle at 40% 45%, var(--photo-light) 0%, #a9abaf 55%, var(--photo-dark) 100%);
  }
  .photo-wide {
    position: absolute;
    left: 40px;
    top: 90px;
    width: 820px;
    height: 330px;
    background: linear-gradient(100deg, #9a9ca1 0%, var(--photo-dark) 35%, #b9bbbe 65%, var(--photo-light) 100%);
    border-radius: 10px;
    opacity: .85;
  }
</style>
</head>
<body>
<main class="sheet">

  <section class="card card--front">
    <div class="brand" style="left:40px; top:34px;">
      <div class="brand__dot"></div>
      <div class="brand__name">Meridian Crestline Motors</div>
    </div>

    <div class="rule" style="left:0; top:208px; width:880px; height:4px;"></div>
    <div class="rule" style="left:706px; top:210px; width:4px; height:263px;"></div>

    <div class="photo-round" role="img" aria-label="Photo of a silver sedan, front three-quarter view"></div>

    <div class="person">
      <span class="person__bar"></span>
      <p class="person__name">Darnell R Okonski</p>
      <p class="person__role">Owner</p>
    </div>

    <ul class="contact">
      <li>
        <svg viewBox="0 0 24 24" aria-hidden="true"><path fill="var(--lime)" d="M6.6 10.8a15.1 15.1 0 0 0 6.6 6.6l2.2-2.2a1 1 0 0 1 1-.25 11.4 11.4 0 0 0 3.6.57 1 1 0 0 1 1 1V20a1 1 0 0 1-1 1A17 17 0 0 1 3 4a1 1 0 0 1 1-1h3.5a1 1 0 0 1 1 1c0 1.25.2 2.45.57 3.6a1 1 0 0 1-.25 1z"/></svg>
        (555) 304-6618
      </li>
      <li>
        <svg viewBox="0 0 24 24" aria-hidden="true"><rect x="2" y="5" width="20" height="14" rx="1.5" fill="none" stroke="var(--lime)" stroke-width="2.4"/><path d="M3 6l9 7 9-7" fill="none" stroke="var(--lime)" stroke-width="2.4"/></svg>
        mercrestmotors@quillbox.example
      </li>
      <li class="plain">Dealer Lic # 48265</li>
    </ul>

    <div class="lime-band"></div>
  </section>

  <section class="card card--back">
    <div class="photo-wide" role="img" aria-label="Photo of three silver sedans parked side by side"></div>

    <div class="brand" style="left:34px; top:20px;">
      <div class="brand__dot"></div>
      <div class="brand__name">Meridian Crestline Motors</div>
    </div>

    <div class="rule" style="left:470px; top:110px; width:410px; height:3px; background:var(--lime);"></div>
    <div class="rule" style="left:0; top:452px; width:880px; height:4px;"></div>

    <div class="lime-band"></div>
  </section>

</main>
</body>
</html>
```